Crisp-Path Administrative Specialists - Website Design | ||
A standard of excellence. A focus on results. | ||
Administrative Services | ||
We are a virtual administrative company, offering executive level services to people in various areas and types of business. We are results-oriented, and place a high value on excellence in service. | ||
We want a look that will attract high-level clientele, but also want to be approachable, and nice to look at. "Crisp Path Administrative Specialists" will be in the header of each page. To give you an idea of the feeling for the website, the logo will be a play on our name. The logo is a medium purple silhouette of a busy female assistant, atop a moving gold globe, while appearing to be busy performing one or two tasks effortlessly. The colors on the website should show off the colors of the logo in the header, and be pleasing to the eye for the rest of the page. The content boxes need to pop out; all the while keeping a professional look to it. We saw a website idea we like in the Web Gallery on this guru website; I have listed it under "web URL" area (it's on page 2, bottom row, middle one; we thought could be viewed as a bouncing board). If you would take the concept of the look and see what you can do for a professional business, OR, come up with a creative idea for our website, that would be great to bounce off and take it to the final concept. When considering the design, think content in a large bubble on the righthand side of the pages; the menu should be in separate clickable bubbles cascading down from the content bubble on the top lefthand side, in different sizes, using the space randomly. This should be done in such a way that it is fun but professional and pleasing. We don't want it to feel "boxy", where everything is in a box on the left, center or right side, which tends to get boring. -There will be a header at top of each page and a border on leftside, rightside and at the bottom. - color in header should show off the purple silhouette and the gold globe, and possibly accommodate the business name in bold letters on each page. - page colors should be cool colors, and show off the bubbles and content in a different color. We have considered a nice cool modern blue, with turquoise and gold. See if you come up with better color scheme! - We will have about 5-7 webpages, so there should be enough bubbles on the home page to accommodate each page. Menu should be identical on each page, with forward/backward navigation, and possibly an area for links. -There will be no pictures in the center of the page; we would like business consulting (people sitting at a table in discussion, office assistants at their PCs, assistants taking phone calls, etc). There should be a background image of an office, maybe. |
Cutting-Edge Unique/Creative Clean/Simple Professional Friendly Exciting Sophisticated Modern Elegant Service Oriented High Tech Fun |
deep medium blue | ||
turquoise (bluish green) | ||
deep rich gold | ||
left side | ||
http://www.markcraftvault.example/Logo-design-portfolio/portfolio.asp?page=2&cat_id=&tab=4#port | ||
we want something different, out of the box, but professional. We want you to get your creative juices flowing and WOW! us, all the while remembering this is a business. |

```html
<!DOCTYPE html>
<html lang="en">
<head>
<meta charset="utf-8">
<title>Crisp-Path Administrative Specialists</title>
<link rel="stylesheet" href="https://fonts.googleapis.com/css2?family=Arimo:ital,wght@0,400;0,700;1,400&family=Tinos:ital@1&display=swap">
<style>
:root{
  --plum-deep:#24041f;
  --plum:#4a0c42;
  --plum-bright:#7a1a6e;
  --maroon:#5a0f22;
  --red:#b3122a;
  --white:#ffffff;
  --soft:#e8d9e6;
  --gold:#f2c23a;
  --sky:#8fd3f0;
  --social:#3b6fb5;
  --footer:#1e031a;
}
*{margin:0;padding:0;box-sizing:border-box}
html,body{width:1200px;height:1018px;overflow:hidden}
body{font-family:"Arimo",Arial,sans-serif;color:var(--white);
  background:radial-gradient(ellipse at 70% 35%,var(--plum-bright) 0%,var(--plum) 40%,var(--plum-deep) 85%);position:relative}
.hero-visual{position:absolute;left:470px;top:0;width:730px;height:545px;
  background:radial-gradient(circle at 62% 62%,#c79bb8 0%,#8a4a80 28%,#4b1346 55%,rgba(36,4,31,0) 78%)}
.brand{position:absolute;left:40px;top:28px;display:flex;align-items:center;gap:20px}
.brand-dot{width:96px;height:96px;border-radius:50%;background:var(--gold)}
.brand-name{font-weight:700;font-size:34px;line-height:42px;color:var(--white)}
.account{position:absolute;right:40px;top:32px;text-align:right;font-size:15px;line-height:21px}
.phone{font-size:22px;font-weight:700;display:flex;align-items:center;gap:8px;justify-content:flex-end;margin-bottom:6px}
.welcome{position:absolute;left:40px;top:245px;width:620px}
.welcome h1{font-weight:400;font-size:56px;margin-bottom:18px}
.welcome p{font-size:13px;line-height:19px;color:var(--soft)}
.nav{position:absolute;left:40px;top:552px;width:1120px;height:40px;
  background:linear-gradient(var(--plum-bright),var(--maroon));display:flex;align-items:center;border-radius:3px}
.nav a{color:var(--white);text-decoration:none;font-size:15px;padding:0 19px;height:40px;line-height:40px;border-right:1px solid rgba(255,255,255,.25)}
.nav a.active{background:var(--red);font-weight:700}
.search{margin-left:auto;display:flex;align-items:center;gap:10px;padding-right:12px;font-weight:700;font-size:15px}
.search span.field{width:270px;height:22px;background:var(--white);border-radius:2px}
.tweet{position:absolute;left:40px;top:615px;width:205px;height:152px;background:var(--white);border:4px solid var(--sky);border-radius:3px;color:#444;padding:6px 8px;font-size:10px;line-height:13px}
.tweet h3{background:var(--sky);color:var(--white);font-size:13px;margin:-6px -8px 5px;padding:3px 8px}
.tweet .time{color:#888;margin-top:4px}
.tweet-by{position:absolute;left:40px;top:775px;display:flex;align-items:center;gap:8px}
.tweet-by .avatar{width:34px;height:34px;border-radius:50%;background:var(--gold)}
.tweet-by b{font-size:14px;display:block}
.tweet-by small{font-size:10px}
.video{position:absolute;top:615px;width:162px;text-align:center;font-size:12px}
.video .thumb{height:125px;background:linear-gradient(#d9d2d6,#6e5a6a);border:2px solid var(--white)}
.video b{display:block;margin-top:7px}
.quote{position:absolute;left:880px;top:615px;width:280px;font-size:13px;line-height:18px}
.quote .mark{font-family:"Tinos",serif;font-size:54px;line-height:30px;display:block}
.quote .mark.close{text-align:right;margin-top:-6px}
.quote .who{color:var(--gold);font-style:italic;margin-top:0}
.quote a{color:var(--gold);display:block;margin-top:10px;font-size:13px}
.share{position:absolute;left:505px;top:828px;width:185px;height:42px;border-radius:4px;
  background:linear-gradient(#f4f4f4,#bdbdbd);color:#555;font-size:21px;text-align:center;line-height:42px}
.footer{position:absolute;left:0;top:885px;width:1200px;height:133px;background:var(--footer);display:flex;padding:22px 40px;font-size:12px;line-height:17px}
.footer h4{font-size:14px;margin-bottom:4px}
.office{width:400px}
.office.right{padding-left:30px;border-left:1px solid rgba(255,255,255,.25)}
.center{width:320px;text-align:center;border-left:1px solid rgba(255,255,255,.25);padding-top:2px}
.social{display:flex;gap:12px;justify-content:center;margin-bottom:10px}
.social span{width:30px;height:30px;border-radius:4px;background:var(--social)}
</style>
</head>
<body>
<div class="hero-visual" role="img" aria-label="Photo of a smiling assistant on the phone at a laptop, in front of a glowing planet"></div>

<header class="brand">
  <div class="brand-dot"></div>
  <div class="brand-name">Crisp-Path<br>Administrative Specialists</div>
</header>

<div class="account">
  <div class="phone"><svg width="22" height="22" viewBox="0 0 24 24"><circle cx="12" cy="12" r="11" fill="#fff"/><path d="M8 6l2 3-1.3 1.3a8 8 0 0 0 5 5L15 14l3 2-1 2.2c-5 .4-10-4.6-9.6-9.6z" fill="#4a0c42"/></svg>800.555.0142</div>
  <div>Login &nbsp;|&nbsp; Register</div>
  <div>Forgot your password?</div>
</div>

<section class="welcome">
  <h1>Welcome to CPAS</h1>
  <p>Lorem ipsum dolor sit amet, consectetur adipiscing elit. Nunc dictum lectus non nulla viverra sed tempus lacus sodales. Etiam malesuada vulputate dictum. Nunc et sem nisi, tempus rhoncus massa. Nam at velit ornare ligula ullamcorper aliquet sed at neque. Etiam scelerisque convallis quam, nec lacinia lorem commodo vitae. Sed at mauris a dolor luctus faucibus. Lorem ipsum dolor sit amet, consectetur adipiscing elit. Nunc dictum lectus non nulla viverra sed tempus lacus sodales.</p>
</section>

<nav class="nav">
  <a class="active">Home</a><a>About Us</a><a>Our Services</a><a>Our Blog</a><a>Contact Us</a>
  <div class="search">Search <span class="field"></span></div>
</nav>

<aside class="tweet">
  <h3>Latest Tweet</h3>
  <p>Lorem ipsum dolor #consectetur adipiscing elit. Nunc dictum lectus non nulla viverra sed tempus lacus sodales. Nunc arcu adipiscing elit mauris ornare velit @sodales #consectetur</p>
  <p class="time">about 16 hours ago</p>
</aside>
<div class="tweet-by"><span class="avatar"></span><div><b>CPAS</b><small>Administrative Specialists</small></div></div>

<div class="video" style="left:260px"><div class="thumb" role="img" aria-label="Video still of a business team meeting"></div><b>Video Title Here</b>00:05:20</div>
<div class="video" style="left:443px"><div class="thumb" role="img" aria-label="Video still of an assistant at her desk"></div><b>Video Title Here</b>00:05:20</div>
<div class="video" style="left:672px"><div class="thumb" role="img" aria-label="Video still of an office assistant working"></div><b>Video Title Here</b>00:05:20</div>

<blockquote class="quote">
  <span class="mark">“</span>
  Lorem ipsum dolor sit amet, consectetur adipiscing elit. Nunc dictum lectus non nulla viverra sed tempus lacus sodales. Etiam malesuada vulputate dictum. Nam at velit ornare ligula ullamcorper aliquet sed at neque.
  <span class="mark close">”</span>
  <div class="who">– Put Name Here –</div>
  <a>Read More</a>
</blockquote>

<div class="share">Share This Site</div>

<footer class="footer">
  <div class="office">
    <h4>Northeast Office:</h4>
    48 Harbor Commons, Suite 210 Riverton, NJ 07099<br>Phone: 800.555.0142
  </div>
  <div class="center">
    <div class="social"><span></span><span></span><span></span><span></span><span></span></div>
    © 2011 Crisp Path. All Rights Reserved.<br>www.crisppath.example
  </div>
  <div class="office right">
    <h4>Southeast Office:</h4>
    2750 Maple Ridge Road, Suite 105 Brookfield, GA 30099<br>Phone: 800.555.0142
  </div>
</footer>
</body>
</html>
```